Business Card Design (NEW FILES)

ATTENTION: New vector files are available. Please update your design to reflect/use the new (better resolution) logo images.

Seeking a unique and professional business card design for a commercial drone photography/videography business. The layout should feature
the logo (attached) and include the following information:
Owen Tarrick
614-502-7738
www.skylarkreelworks.example
NRD Certified Remote Pilot

Owen Tarrick

```html
<!DOCTYPE html>
<html lang="en">
<head>
<meta charset="utf-8">
<title>Skylark Reelworks – Business Card</title>
<link rel="stylesheet" href="https://fonts.googleapis.com/css2?family=Open+Sans:wght@400;600;800&display=swap">
<style>
  :root {
    --stage: #232323;
    --navy: #18194a;
    --navy-deep: #141640;
    --navy-glow: #2b3f9e;
    --white: #ffffff;
    --orange: #ea8a50;
    --teal: #17b4b4;
  }
  * { margin: 0; padding: 0; box-sizing: border-box; }
  html, body { width: 1200px; height: 780px; overflow: hidden; background: var(--stage); }
  body { position: relative; font-family: "Open Sans", sans-serif; }

  .card {
    position: absolute;
    width: 560px;
    height: 320px;
    border-radius: 22px;
    overflow: hidden;
  }
  .card--back { left: 40px; top: 60px; background: var(--navy-deep); }
  .card--front { left: 600px; top: 400px; background: var(--white); }

  .back-illustration {
    position: absolute;
    left: 60px; top: 24px;
    width: 460px; height: 250px;
    border-radius: 50%;
    background: radial-gradient(ellipse at 55% 40%, var(--navy-glow) 0%, #1d2670 45%, var(--navy-deep) 75%);
    opacity: 0.85;
  }

  .brand {
    position: absolute;
    display: flex;
    align-items: center;
    gap: 8px;
    font-weight: 600;
    font-size: 20px;
    letter-spacing: 0.5px;
    white-space: nowrap;
  }
  .brand__dot { width: 13px; height: 13px; border-radius: 50%; background: currentColor; flex: none; }
  .card--back .brand { left: 150px; top: 234px; color: var(--white); }
  .card--front .brand { left: 36px; top: 70px; color: var(--navy); }

  .front-wave { position: absolute; inset: 0; width: 560px; height: 320px; }

  .contact {
    position: absolute;
    right: 30px; top: 96px;
    text-align: right;
    color: var(--white);
    white-space: nowrap;
  }
  .contact__name { font-size: 27px; font-weight: 800; line-height: 1; }
  .contact__name .first { color: var(--orange); }
  .contact__role { font-size: 12px; font-weight: 600; margin-top: 4px; }
  .contact__creds { font-size: 12px; line-height: 1.45; margin-top: 16px; }
  .contact__lines { margin-top: 12px; font-size: 12px; line-height: 1.6; }
  .contact__line { display: flex; align-items: center; justify-content: flex-end; gap: 8px; }
  .contact__line svg { width: 12px; height: 12px; flex: none; }
</style>
</head>
<body>

  <section class="card card--back" aria-label="Card back">
    <div class="back-illustration" role="img" aria-label="Large embossed drone illustration with camera lens"></div>
    <div class="brand"><span class="brand__dot"></span>Skylark Reelworks</div>
  </section>

  <section class="card card--front" aria-label="Card front">
    <svg class="front-wave" viewBox="0 0 560 320" aria-hidden="true">
      <path d="M406 0 C336 10 276 80 246 160 C216 240 126 300 16 320 L560 320 L560 0 Z" fill="var(--orange)"/>
      <path d="M420 0 C350 10 290 80 260 160 C230 240 140 300 30 320 L560 320 L560 0 Z" fill="var(--white)"/>
      <path d="M428 0 C358 10 298 80 268 160 C238 240 148 300 38 320 L560 320 L560 0 Z" fill="var(--teal)"/>
      <path d="M440 0 C370 10 310 80 280 160 C250 240 160 300 50 320 L560 320 L560 0 Z" fill="var(--white)"/>
      <path d="M450 0 C380 10 320 80 290 160 C260 240 170 300 60 320 L560 320 L560 0 Z" fill="var(--navy)"/>
    </svg>

    <div class="brand"><span class="brand__dot"></span>Skylark Reelworks</div>

    <div class="contact">
      <div class="contact__name"><span class="first">Owen</span> Tarrick</div>
      <div class="contact__role">Owner</div>
      <div class="contact__creds">NRD Certified Remote Pilot<br>Fully Insured</div>
      <div class="contact__lines">
        <div class="contact__line">614-502-7738
          <svg viewBox="0 0 24 24"><path fill="var(--orange)" d="M6.6 10.8a15 15 0 0 0 6.6 6.6l2.2-2.2a1 1 0 0 1 1-.25 11.4 11.4 0 0 0 3.6.57 1 1 0 0 1 1 1V20a1 1 0 0 1-1 1A17 17 0 0 1 3 4a1 1 0 0 1 1-1h3.5a1 1 0 0 1 1 1c0 1.25.2 2.45.57 3.57a1 1 0 0 1-.25 1z"/></svg>
        </div>
        <div class="contact__line">www.skylarkreelworks.example
          <svg viewBox="0 0 24 24"><circle cx="12" cy="12" r="10" fill="none" stroke="var(--orange)" stroke-width="2.4"/><path d="M2 12h20M12 2c3 3 3 17 0 20M12 2c-3 3-3 17 0 20" fill="none" stroke="var(--orange)" stroke-width="2"/></svg>
        </div>
      </div>
    </div>
  </section>

</body>
</html>
```